Logo + Label Design (Men’s Grooming Brand & Product Packaging)

Design a logo and 2 oz pomade label for Brel, a modern men’s grooming brand focused on clean, high-quality, natural ingredients. The design should establish a bold, masculine, minimalist identity that can later extend to products like shaving gel and body wash.

Key Requirements

Create a primary logo for “Brel” and a core label for the 2 oz pomade jar (screw-top).

Use a clean, modern style — masculine, confident, and approachable (think Dorran’s, Velta, Northfield Kit).

Design for 1–2 color screen printing on solid jar colors (white, black, or navy).

Avoid gradients, foil, or embossing. Must work in black & white.

Provide: vector logo, mockup of the 2 oz jar, color palette (CMYK/RGB/HEX), and font specs.

Winning design may lead to future projects (body wash, shave gel, skincare lines).

Font styles to use
Other font styles liked:
• We like the fonts and design concept in the attached mockup.

Requirements
Should not have
• We want to avoid too much writing or busy designs. We want to avoid having graphics/illustrations embedded in the logo if they will cause the brand to look less classy or sophisticated. We also want the design to look simple and all-American (e.g. Hollister and Vane, Pine Ledger, The KIM, etc). We’d like to give a Pellham & Royce vibe that feels classy and high end.

```html
<!DOCTYPE html>
<html lang="en">
<head>
<meta charset="utf-8">
<title>Brel Hair Pomade – Label</title>
<link href="https://fonts.googleapis.com/css2?family=Playfair+Display:wght@400;700&family=Libre+Baskerville:wght@400&display=swap" rel="stylesheet">
<style>
  :root {
    --bg: #ececec;
    --label: #2d2d2e;
    --lid: #2b2c2e;
    --lid-edge: #1f2022;
    --ink: #ffffff;
    --ink-soft: #d9d9d9;
    --accent: #4f93d8;
  }
  * { margin: 0; padding: 0; box-sizing: border-box; }
  html, body { width: 1200px; height: 1200px; overflow: hidden; }
  body { background: var(--bg); position: relative; font-family: "Libre Baskerville", Georgia, serif; color: var(--ink); }

  /* Wraparound jar label, unrolled */
  .jar-label {
    position: absolute; left: 50px; top: 120px; width: 1100px; height: 340px;
    background: var(--label);
  }
  .info-panel {
    position: absolute; left: 36px; top: 44px; width: 300px;
    font-size: 12.5px; line-height: 21px; text-align: justify; color: var(--ink-soft);
  }
  .info-panel h3 { font-family: "Playfair Display", Georgia, serif; font-weight: 700; font-size: 13px; letter-spacing: 1px; text-transform: uppercase; color: var(--ink); margin-bottom: 4px; }
  .info-panel p + h3 { margin-top: 18px; }
  .rule { position: absolute; top: 40px; height: 260px; width: 1px; background: var(--ink-soft); }
  .rule.left { left: 372px; }
  .rule.right { left: 752px; }
  .wordmark {
    position: absolute; left: 372px; width: 380px; top: 70px; text-align: center;
    font-family: "Playfair Display", Georgia, serif; font-weight: 700; font-size: 150px; line-height: 1; color: var(--ink);
  }
  .product-type {
    position: absolute; left: 790px; top: 170px; transform: translate(-50%, -50%) rotate(-90deg);
    font-family: "Playfair Display", Georgia, serif; font-weight: 700; font-size: 22px; letter-spacing: 1px; color: var(--ink-soft); white-space: nowrap;
  }
  .spec-panel { position: absolute; left: 840px; top: 74px; }
  .spec-panel .finish { font-family: "Playfair Display", Georgia, serif; font-weight: 700; font-size: 22px; line-height: 28px; }
  .spec-panel .scent { font-size: 22px; color: var(--accent); margin-top: 30px; }
  .spec-panel .net { font-size: 13px; letter-spacing: 1px; color: var(--ink-soft); margin-top: 70px; }

  /* Screw-top lid */
  .lid {
    position: absolute; left: 350px; top: 580px; width: 500px; height: 500px; border-radius: 50%;
    background: var(--lid); border: 14px solid var(--lid-edge);
  }
  .lid-inner { position: absolute; inset: 22px; border-radius: 50%; border: 1px solid #3c3d40; }
  .lid .rule { left: 200px; top: 90px; height: 290px; }
  .lid .product-type { left: 170px; top: 300px; font-size: 22px; color: var(--ink); }
  .lid-brand { position: absolute; left: 222px; top: 92px; font-family: "Playfair Display", Georgia, serif; font-weight: 700; font-size: 76px; line-height: 1; }
  .lid-finish { position: absolute; left: 226px; top: 196px; font-family: "Playfair Display", Georgia, serif; font-weight: 700; font-size: 17px; line-height: 22px; }
  .lid-scent { position: absolute; left: 226px; top: 256px; font-size: 17px; color: var(--accent); }
  .lid-net { position: absolute; left: 226px; top: 350px; font-size: 11px; color: var(--ink-soft); }
</style>
</head>
<body>
  <section class="jar-label" aria-label="Brel hair pomade jar label">
    <div class="info-panel">
      <h3>Directions</h3>
      <p>Warm a small amount of pomade between hands and apply to damp hair (for a sleeker look) or dry hair (for a textured look). For external use only. Avoid contact with eyes. If irritation occurs, discontinue use.</p>
      <h3>Ingredients</h3>
      <p>Butyrospermum Parkii (Shea Butter), Cera Alba (Beeswax), Cera Bellina, Caprylic/Capric Triglyceride, Kaolin (Clay), Tocopherol (Vitamin E), Parfum.</p>
    </div>
    <span class="rule left"></span>
    <div class="wordmark">brel</div>
    <span class="rule right"></span>
    <div class="product-type">Hair Pomade</div>
    <div class="spec-panel">
      <div class="finish">Matte Finish<br>Medium Hold</div>
      <div class="scent">Fresh &amp; Clean</div>
      <div class="net">2 oz (57 g)</div>
    </div>
  </section>

  <section class="lid" aria-label="Brel hair pomade lid label">
    <div class="lid-inner"></div>
    <span class="rule"></span>
    <div class="product-type">Hair Pomade</div>
    <div class="lid-brand">brel</div>
    <div class="lid-finish">Matte Finish<br>Medium Hold</div>
    <div class="lid-scent">Fresh &amp; Clean</div>
    <div class="lid-net">2 oz (57 g)</div>
  </section>
</body>
</html>
```